Harborline Auto LLC

Car Dealer Customer Service
Address: 2874 Cresthaven Road, Shelbyville, TN 37162
web: www.harborlineautoxq.net
email: harborlineautoxq@mailnest.example
Phone: (931) 555-0148
Phone: (629) 555-0173

```html
<!DOCTYPE html>
<html lang="en">
<head>
<meta charset="utf-8">
<title>Harborline Auto – Business Cards</title>
<link href="https://fonts.googleapis.com/css2?family=Montserrat:wght@500;700;800&family=Arimo:wght@400;700&display=swap" rel="stylesheet">
<style>
  :root {
    --page-bg: #1d1d1f;
    --card-bg: #0b0b0c;
    --brand-blue: #2a8fd0;
    --brand-gold: #f0b544;
    --text-light: #f2f2f2;
    --divider: #5a5a5a;
  }
  * { box-sizing: border-box; margin: 0; padding: 0; }
  html, body {
    width: 1200px; height: 900px; overflow: hidden;
    background: var(--page-bg);
  }
  .canvas { position: relative; width: 1200px; height: 900px; }

  .card {
    position: absolute;
    width: 580px; height: 330px;
    background: var(--card-bg);
    box-shadow: 0 18px 40px rgba(0,0,0,0.6);
  }
  .card--back { left: 570px; top: 90px; }
  .card--front { left: 50px; top: 480px; }

  /* Brand block */
  .brand { display: flex; flex-direction: column; align-items: center; }
  .brand__mark {
    width: 92px; height: 92px; border-radius: 50%;
    background: var(--brand-blue);
    margin-bottom: 18px;
  }
  .brand__name {
    font-family: "Montserrat", sans-serif;
    font-weight: 800;
    color: var(--brand-blue);
    letter-spacing: 1px;
    white-space: nowrap;
  }
  .brand__tagline {
    font-family: "Montserrat", sans-serif;
    font-weight: 500;
    color: var(--brand-gold);
    font-size: 14px;
    letter-spacing: 1.6px;
    margin-top: 6px;
  }

  .card--back .brand {
    position: absolute; inset: 0;
    justify-content: center;
  }
  .card--back .brand__name { font-size: 36px; }

  .card--front .brand {
    position: absolute; left: 30px; top: 0; bottom: 0; width: 250px;
    justify-content: center;
  }
  .card--front .brand__mark { width: 78px; height: 78px; }
  .card--front .brand__name { font-size: 25px; }

  .card__divider {
    position: absolute; left: 292px; top: 55px;
    width: 1px; height: 220px; background: var(--divider);
  }

  .contact {
    position: absolute; left: 318px; top: 48px; right: 18px;
    font-family: "Arimo", sans-serif;
    color: var(--text-light);
  }
  .contact__name {
    font-family: "Montserrat", sans-serif;
    font-weight: 800; font-size: 19px;
    color: var(--brand-blue); letter-spacing: .5px;
  }
  .contact__role { font-size: 14px; margin-bottom: 14px; }
  .contact__list { list-style: none; }
  .contact__item {
    display: flex; align-items: center; gap: 8px;
    font-size: 13.5px; line-height: 22px; white-space: nowrap;
  }
  .contact__item svg { width: 14px; height: 14px; flex: none; fill: var(--brand-blue); }
  .contact__highlight { color: var(--brand-blue); }
  .contact__address { margin-top: 14px; font-size: 14.5px; line-height: 21px; }
</style>
</head>
<body>
<main class="canvas">

  <section class="card card--back" aria-label="Business card, back">
    <div class="brand">
      <div class="brand__mark"></div>
      <div class="brand__name">HARBORLINE AUTO</div>
      <div class="brand__tagline">CAR DEALER CUSTOMER SERVICE</div>
    </div>
  </section>

  <section class="card card--front" aria-label="Business card, front">
    <div class="brand">
      <div class="brand__mark"></div>
      <div class="brand__name">HARBORLINE AUTO</div>
    </div>

    <div class="card__divider"></div>

    <div class="contact">
      <div class="contact__name">MARCUS DELANEY</div>
      <div class="contact__role">Managing Director</div>
      <ul class="contact__list">
        <li class="contact__item">
          <svg viewBox="0 0 24 24" aria-hidden="true"><path d="M6.6 10.8a15.1 15.1 0 0 0 6.6 6.6l2.2-2.2a1 1 0 0 1 1-.25 11.4 11.4 0 0 0 3.6.57 1 1 0 0 1 1 1V20a1 1 0 0 1-1 1A17 17 0 0 1 3 4a1 1 0 0 1 1-1h3.5a1 1 0 0 1 1 1c0 1.25.2 2.45.57 3.6a1 1 0 0 1-.25 1z"/></svg>
          (931) 555-0148
        </li>
        <li class="contact__item">
          <svg viewBox="0 0 24 24" aria-hidden="true"><path d="M6.6 10.8a15.1 15.1 0 0 0 6.6 6.6l2.2-2.2a1 1 0 0 1 1-.25 11.4 11.4 0 0 0 3.6.57 1 1 0 0 1 1 1V20a1 1 0 0 1-1 1A17 17 0 0 1 3 4a1 1 0 0 1 1-1h3.5a1 1 0 0 1 1 1c0 1.25.2 2.45.57 3.6a1 1 0 0 1-.25 1z"/></svg>
          (629) 555-0173
        </li>
        <li class="contact__item">
          <svg viewBox="0 0 24 24" aria-hidden="true"><path d="M12 2a10 10 0 1 0 0 20 10 10 0 0 0 0-20zm6.9 6h-2.9a15.7 15.7 0 0 0-1.4-3.6A8 8 0 0 1 18.9 8zM12 4c.8 1.2 1.5 2.5 1.9 4h-3.8c.4-1.5 1.1-2.8 1.9-4zM4.3 14a8.2 8.2 0 0 1 0-4h3.4a16.5 16.5 0 0 0 0 4zm.8 2h2.9c.3 1.3.8 2.5 1.4 3.6A8 8 0 0 1 5.1 16zM8 8H5.1a8 8 0 0 1 4.3-3.6C8.8 5.5 8.4 6.7 8 8zm4 12c-.8-1.2-1.5-2.5-1.9-4h3.8c-.4 1.5-1.1 2.8-1.9 4zm2.3-6H9.7a14.7 14.7 0 0 1 0-4h4.6a14.7 14.7 0 0 1 0 4zm.3 5.6c.6-1.1 1.1-2.3 1.4-3.6h2.9a8 8 0 0 1-4.3 3.6zm1.7-5.6a16.5 16.5 0 0 0 0-4h3.4a8.2 8.2 0 0 1 0 4z"/></svg>
          <span>www.<span class="contact__highlight">harborlineautoxq</span>.net</span>
        </li>
        <li class="contact__item">
          <svg viewBox="0 0 24 24" aria-hidden="true"><path d="M2 5h20v14H2zm2 2v.4l8 5.1 8-5.1V7zm0 2.8V17h16V9.8l-8 5.1z"/></svg>
          harborlineautoxq@mailnest.example
        </li>
      </ul>
      <p class="contact__address">2874 Cresthaven Road<br>Shelbyville, TN 37162</p>
    </div>
  </section>

</main>
</body>
</html>
```